Brookvale Building Company - advertisement poster

I am looking to print some canvas signs to advertise my general contracting company, Brookvale Building Company. The sign will measure 6' long x 3' high so the size should match that ratio. I already have a logo icon, which is the Letter 'B' and some trees that I would like to incorporate, see attached. I would also like the to have the following information listed:
1) phone number: 831-555-0172
2) email: brookvalebuildingcompany@mailnest.example
3) website: brookvalebuildingcompany.example
4) Lic#4826130
5) I want to use this text: "BUILD WITH THE B-CREW!"

The ad should be relatively simple and clean. Black and Green are my company colors. I am open to creative ideas!

Target Market(s)

People looking to renovate their homes

Industry/Entity Type

Construction

Colors
59FF00
82FF00
B8FF75
E3FFCB
F4FFEA

Requirements
Must have
• Must have my company logo
Should not have
• No photos or complex graphics

```html
<!DOCTYPE html>
<html lang="en">
<head>
<meta charset="UTF-8">
<title>Brookvale Building Company – Sign</title>
<link href="https://fonts.googleapis.com/css2?family=Archivo+Black&family=Montserrat:wght@400;500;600;700;800&display=swap" rel="stylesheet">
<style>
  :root {
    --brand-green: #6cb33f;
    --brand-black: #1e1e1e;
    --ink: #1a1a1a;
    --white: #ffffff;
    --backdrop: #e9ece6;
  }
  * { margin: 0; padding: 0; box-sizing: border-box; }
  html, body {
    width: 1200px; height: 800px; overflow: hidden;
    background: var(--backdrop);
  }
  .canvas {
    width: 1200px; height: 800px;
    display: flex; align-items: center; justify-content: center;
  }
  .sign {
    width: 1120px; height: 560px;
    display: flex;
    box-shadow: 0 10px 30px rgba(0,0,0,0.18);
  }
  .sign__message {
    width: 644px; height: 100%;
    background: var(--brand-green);
    position: relative;
    padding: 120px 0 0 56px;
  }
  .headline {
    font-family: "Archivo Black", "Arial Black", sans-serif;
    color: var(--ink);
    font-size: 102px;
    line-height: 0.93;
    letter-spacing: -1px;
  }
  .headline span { display: block; }
  .license {
    position: absolute; left: 58px; bottom: 52px;
    font-family: "Montserrat", sans-serif;
    font-weight: 500;
    font-size: 15px;
    color: var(--ink);
  }
  .sign__contact {
    flex: 1; height: 100%;
    background: var(--brand-black);
    display: flex; flex-direction: column; align-items: center;
    padding-top: 132px;
  }
  .brand-name {
    display: flex; align-items: center; gap: 14px;
    font-family: "Montserrat", sans-serif;
    font-weight: 800;
    font-size: 30px;
    line-height: 1.1;
    color: var(--white);
    text-transform: uppercase;
    letter-spacing: 1px;
  }
  .brand-name__mark {
    width: 22px; height: 22px;
    background: var(--brand-green);
    flex: none;
  }
  .contact-list {
    margin-top: 78px;
    width: 400px;
    display: flex; flex-direction: column; align-items: flex-end;
    font-family: "Montserrat", sans-serif;
  }
  .contact-row { display: flex; align-items: center; gap: 14px; }
  .contact-row svg { flex: none; }
  .phone {
    font-weight: 700;
    font-size: 48px;
    color: var(--brand-green);
    letter-spacing: 0.5px;
  }
  .email {
    margin-top: 14px;
    font-weight: 400;
    font-size: 17px;
    color: var(--white);
    letter-spacing: 0.3px;
  }
  .website {
    margin-top: 18px;
    font-weight: 700;
    font-size: 19px;
    color: var(--white);
  }
</style>
</head>
<body>
<main class="canvas">
  <section class="sign">
    <div class="sign__message">
      <h1 class="headline">
        <span>Build</span>
        <span>with the</span>
        <span>B-CREW!</span>
      </h1>
      <p class="license">License No. 4826130</p>
    </div>
    <div class="sign__contact">
      <div class="brand-name">
        <span class="brand-name__mark"></span>
        <span>Brookvale<br>Building Company</span>
      </div>
      <div class="contact-list">
        <div class="contact-row">
          <svg width="36" height="36" viewBox="0 0 36 36" aria-hidden="true">
            <circle cx="18" cy="18" r="16" fill="none" stroke="#6cb33f" stroke-width="2"/>
            <path d="M12.5 10.5c1-.8 2-.6 2.6.3l1.6 2.4c.5.8.3 1.6-.4 2.2l-1 .8c.9 2 2.5 3.6 4.5 4.5l.8-1c.6-.7 1.4-.9 2.2-.4l2.4 1.6c.9.6 1.1 1.6.3 2.6l-1 1.2c-.8 1-2.4 1.3-4 .6-4.3-1.9-7.6-5.2-9.5-9.5-.7-1.6-.4-3.2.6-4z" fill="#6cb33f"/>
          </svg>
          <span class="phone">831.555.0172</span>
        </div>
        <p class="email">brookvalebuildingcompany@mailnest.example</p>
        <div class="contact-row website">
          <svg width="24" height="24" viewBox="0 0 24 24" aria-hidden="true" fill="none" stroke="#6cb33f" stroke-width="1.6">
            <circle cx="12" cy="12" r="10"/>
            <ellipse cx="12" cy="12" rx="4.5" ry="10"/>
            <line x1="2" y1="12" x2="22" y2="12"/>
            <path d="M4 6.5h16M4 17.5h16"/>
          </svg>
          <span>BrookvaleBuildingCompany.example</span>
        </div>
      </div>
    </div>
  </section>
</main>
</body>
</html>
```